Business cards for Harbourline Supply Pty Ltd that import building products into Australia from China
Target Market(s)
Business to Business
Industry/Entity Type
Business
Contact Information for Business Card
Front: Logo and Business Name
Rear:
Desmond Varrick
General Manager
Mobile: 0427 561 394
email: dessie@harbourlinesupply.com.au
alternative email: dessie@outbackworks.com.au
web: www.harbourlinesupply.com.au
Adelaide, Brisbane and Darwin
Colors
ec1f27
fbee3d

```html
<!DOCTYPE html>
<html lang="en">
<head>
<meta charset="utf-8">
<title>Harbourline Supply Pty Ltd – Business Cards</title>
<link rel="stylesheet" href="https://fonts.googleapis.com/css2?family=Montserrat:wght@400;500;600&display=swap">
<style>
  :root {
    --brand-red: #ec1f27;
    --ink: #3a3a3c;
    --card: #ffffff;
    --stage: #2e2e30;
  }
  * { margin: 0; padding: 0; box-sizing: border-box; }
  html, body { width: 1200px; height: 864px; overflow: hidden; }
  body {
    background: var(--stage);
    font-family: "Montserrat", sans-serif;
    color: var(--ink);
    display: flex;
    flex-direction: column;
    align-items: center;
    justify-content: center;
    gap: 28px;
  }
  .card {
    width: 700px;
    height: 400px;
    background: var(--card);
    border-radius: 26px;
    position: relative;
    box-shadow: 0 10px 30px rgba(0,0,0,.45);
  }
  .brand {
    display: flex;
    align-items: center;
    gap: 14px;
  }
  .brand-mark {
    width: 22px; height: 22px;
    background: var(--brand-red);
    flex: none;
  }
  .brand-name {
    color: var(--brand-red);
    font-weight: 600;
    font-size: 30px;
    letter-spacing: .5px;
    line-height: 1.15;
  }

  /* Front */
  .card-front .brand {
    position: absolute;
    top: 150px; left: 0; right: 0;
    justify-content: center;
  }
  .locations {
    position: absolute;
    bottom: 46px; left: 0; right: 0;
    text-align: center;
    font-size: 15px;
  }
  .locations .dot {
    display: inline-block;
    width: 5px; height: 5px;
    border-radius: 50%;
    background: var(--brand-red);
    margin: 0 6px 3px;
  }

  /* Back */
  .card-back { display: flex; align-items: center; padding: 0 40px 0 46px; }
  .card-back .brand { width: 300px; }
  .card-back .brand-name { font-size: 25px; }
  .divider {
    width: 2px; height: 200px;
    background: var(--brand-red);
    margin: 0 26px 0 14px;
    flex: none;
  }
  .person-name { color: var(--brand-red); font-weight: 600; font-size: 23px; }
  .person-role { font-size: 15px; margin-top: 2px; margin-bottom: 22px; }
  .contact-list { list-style: none; font-size: 14.5px; }
  .contact-list li { display: flex; align-items: center; gap: 10px; margin-top: 6px; }
  .contact-list svg { width: 15px; height: 15px; flex: none; }
</style>
</head>
<body>
  <section class="card card-front">
    <div class="brand">
      <span class="brand-mark"></span>
      <span class="brand-name">Harbourline Supply Pty Ltd</span>
    </div>
    <p class="locations">Adelaide<span class="dot"></span>Brisbane<span class="dot"></span>Darwin</p>
  </section>

  <section class="card card-back">
    <div class="brand">
      <span class="brand-mark"></span>
      <span class="brand-name">Harbourline Supply<br>Pty Ltd</span>
    </div>
    <div class="divider"></div>
    <div class="contact">
      <p class="person-name">Desmond Varrick</p>
      <p class="person-role">General Manager</p>
      <ul class="contact-list">
        <li>
          <svg viewBox="0 0 16 16" aria-hidden="true"><rect x="4" y="1" width="8" height="14" rx="1.5" fill="none" stroke="#ec1f27" stroke-width="1.6"/><circle cx="8" cy="12.3" r=".9" fill="#ec1f27"/></svg>
          0427 561 394
        </li>
        <li>
          <svg viewBox="0 0 16 16" aria-hidden="true"><rect x="1" y="3" width="14" height="10" fill="#ec1f27"/><path d="M1 3l7 6 7-6" fill="none" stroke="#fff" stroke-width="1.3"/></svg>
          dessie@harbourlinesupply.com.au
        </li>
        <li>
          <svg viewBox="0 0 16 16" aria-hidden="true"><rect x="1" y="3" width="14" height="10" fill="#ec1f27"/><path d="M1 3l7 6 7-6" fill="none" stroke="#fff" stroke-width="1.3"/></svg>
          dessie@outbackworks.com.au
        </li>
        <li>
          <svg viewBox="0 0 16 16" aria-hidden="true"><circle cx="8" cy="8" r="6.5" fill="none" stroke="#ec1f27" stroke-width="1.5"/><ellipse cx="8" cy="8" rx="2.8" ry="6.5" fill="none" stroke="#ec1f27" stroke-width="1.2"/><path d="M1.5 8h13" stroke="#ec1f27" stroke-width="1.2"/></svg>
          www.harbourlinesupply.com.au
        </li>
      </ul>
    </div>
  </section>
</body>
</html>
```